Advertising company unique advertising platform

we need a logo design for a new company based in Australia Melbourne. We develop innovated advertising platform where consumer can use this platform to get regular discount, as business owner they can use this platform for free advertisement. Payment for this advertisement platform only payable every two weeks, when I generate revenue for their business

Industry/Entity Type

Advertising

Contact Information for Business Card

Dale Morven | Co-Founder |Managing Director
Suite 718 240 Wattlebrook Lane Melbourne Vic 3000

ABN 38 614 207 923
Tel: +61 0487 259 318 | Email: dale.morven@plivorantu.com

Font styles to use
Decorative
Script

Requirements
Must have
• Try few different design and some round corner business card
Should not have
• One round corner business card...try 4 different colour background not only black, make sure two side is designed. Be creative so imagine you are giving this to a client make sure has wow factor, if you can also try one design with engrave like all the logo, words look 3d feel
• The word Advertising Platform use attached file font

```html
<!DOCTYPE html>
<html lang="en">
<head>
<meta charset="utf-8">
<title>Onevale Hub – Business Card</title>
<link rel="stylesheet" href="https://fonts.googleapis.com/css2?family=Open+Sans:wght@400;600;700&display=swap">
<style>
  :root {
    --backdrop: #0b0b0b;
    --card: #282828;
    --card-edge: #303030;
    --accent: #f0891d;
    --text-muted: #b9b9b9;
    --brand: #f0891d;
    --ghost: #313131;
  }
  * { margin: 0; padding: 0; box-sizing: border-box; }
  html, body {
    width: 1200px; height: 1000px; overflow: hidden;
    background: var(--backdrop);
    font-family: "Open Sans", Arial, sans-serif;
  }
  .stage {
    position: relative; width: 1200px; height: 1000px;
    display: flex; align-items: center; justify-content: center; gap: 60px;
  }
  .card {
    position: relative; width: 525px; height: 300px;
    background: var(--card);
    border: 1px solid var(--card-edge);
    box-shadow: 0 18px 40px rgba(0,0,0,.6);
    overflow: hidden;
  }
  /* front */
  .identity { position: absolute; left: 34px; top: 34px; }
  .identity__name { color: var(--accent); font-weight: 700; font-size: 19px; line-height: 1.2; }
  .identity__role { color: var(--text-muted); font-size: 12.5px; margin-top: 2px; }
  .contact { position: absolute; left: 34px; top: 140px; list-style: none; }
  .contact__item {
    display: flex; align-items: flex-start; gap: 8px;
    color: var(--text-muted); font-size: 12.5px; line-height: 1.45;
  }
  .contact__icon { width: 11px; height: 11px; margin-top: 3px; flex: none; fill: var(--accent); }
  .brand-mark {
    display: flex; align-items: center; gap: 8px;
    color: var(--brand); font-weight: 700; white-space: nowrap;
  }
  .brand-mark__dot { border-radius: 50%; background: var(--brand); flex: none; }
  .brand-mark--small { position: absolute; right: 34px; top: 118px; font-size: 20px; }
  .brand-mark--small .brand-mark__dot { width: 16px; height: 16px; }
  .abn { position: absolute; right: 34px; bottom: 26px; color: var(--accent); font-size: 13px; }
  /* back */
  .brand-mark--large { position: absolute; left: 56px; top: 128px; font-size: 34px; z-index: 1; }
  .brand-mark--large .brand-mark__dot { width: 26px; height: 26px; }
  .ghost-circle {
    position: absolute; right: 26px; bottom: 18px;
    width: 130px; height: 130px; border-radius: 50%;
    background: var(--ghost);
  }
</style>
</head>
<body>
<main class="stage">
  <section class="card card--front" aria-label="Business card front">
    <div class="identity">
      <p class="identity__name">Dale Morven</p>
      <p class="identity__role">Co-Founder | Managing Director</p>
    </div>
    <ul class="contact">
      <li class="contact__item">
        <svg class="contact__icon" viewBox="0 0 12 12" aria-hidden="true"><path d="M2.5 0.5l2 2.6-1.2 1.3c.7 1.6 2 2.9 3.4 3.6l1.3-1.2 2.5 2-1.2 2.2C4.6 10.5 1.3 7.2.3 2z"/></svg>
        <span>+61 0487 259 318</span>
      </li>
      <li class="contact__item">
        <svg class="contact__icon" viewBox="0 0 12 12" aria-hidden="true"><path d="M0 2h12v8H0z M0 2l6 4.5L12 2" stroke="#282828" stroke-width="1"/></svg>
        <span>dale.morven@plivorantu.com</span>
      </li>
      <li class="contact__item">
        <svg class="contact__icon" viewBox="0 0 12 12" aria-hidden="true"><path d="M6 0a4 4 0 0 1 4 4c0 3-4 8-4 8S2 7 2 4a4 4 0 0 1 4-4zm0 2.3a1.7 1.7 0 1 0 0 3.4 1.7 1.7 0 0 0 0-3.4z"/></svg>
        <span>Suite 718 240 Wattlebrook Lane<br>Melbourne Vic 3000</span>
      </li>
    </ul>
    <div class="brand-mark brand-mark--small">
      <span class="brand-mark__dot"></span><span>Onevale Hub</span>
    </div>
    <p class="abn">ABN 38 614 207 923</p>
  </section>

  <section class="card card--back" aria-label="Business card back">
    <div class="brand-mark brand-mark--large">
      <span class="brand-mark__dot"></span><span>Onevale Hub</span>
    </div>
    <div class="ghost-circle" aria-hidden="true"></div>
  </section>
</main>
</body>
</html>
```